Business Card Design Project

I need a business card designed from scratch. I have an existing logo that I can upload in Illustrator for modification or redesign.

The Company is called Query Lanterns http://querylanterns.com.au and we provide Search Engine Optimization services to Australian businesses. The current logo signifies an increase in visitors, profits etc...

There are no restrictions as to the redesign - colours, style etc are all open to change.

Cards will be full colour and one sided printed at http://www.cardmoxel.com.au so check their requirements for file format and sizes etc.

I will expect all original files upon completion of project.

Target Market(s)

Any business with a web site looking to improve their search engine rankings

Industry/Entity Type

Business

Requirements
Must have
• I like modern, sleek designs. Clean, not fussy, uncluttered.

```html
<!DOCTYPE html>
<html lang="en">
<head>
<meta charset="utf-8">
<title>Query Lanterns – Business Card</title>
<link href="https://fonts.googleapis.com/css2?family=Open+Sans:wght@600;700;800&display=swap" rel="stylesheet">
<style>
  :root {
    --brand-blue: #1d6db3;
    --deep-blue: #1a4f8f;
    --brand-yellow: #f2c318;
    --text-yellow: #e3b912;
    --card-white: #ffffff;
    --backdrop: #e4e5e7;
    --card-edge: rgba(0,0,0,0.10);
  }
  * { margin: 0; padding: 0; box-sizing: border-box; }
  html, body {
    width: 1187px;
    height: 1200px;
    overflow: hidden;
    background: var(--backdrop);
    font-family: "Open Sans", Arial, sans-serif;
  }
  .canvas {
    position: relative;
    width: 1187px;
    height: 1200px;
  }
  .card {
    position: absolute;
    left: 221px;
    width: 727px;
    height: 471px;
    background: var(--card-white);
    box-shadow: 0 2px 10px rgba(0,0,0,0.18), inset 0 0 40px var(--card-edge);
    overflow: hidden;
  }
  .card--front { top: 73px; }
  .card--back { top: 641px; }

  /* Front */
  .front-brand {
    position: absolute;
    left: 0;
    right: 0;
    top: 196px;
    display: flex;
    align-items: center;
    justify-content: center;
    gap: 22px;
  }
  .brand-dot {
    width: 46px;
    height: 46px;
    border-radius: 50%;
    background: var(--brand-yellow);
    flex: none;
  }
  .brand-name {
    font-weight: 800;
    color: var(--brand-blue);
    letter-spacing: -0.5px;
    line-height: 1;
    white-space: nowrap;
  }
  .front-brand .brand-name { font-size: 68px; }

  /* Back */
  .back-brand {
    position: absolute;
    left: 24px;
    top: 332px;
    display: flex;
    align-items: center;
    gap: 10px;
  }
  .back-brand .brand-dot { width: 20px; height: 20px; }
  .back-brand .brand-name { font-size: 27px; }
  .divider {
    position: absolute;
    left: 319px;
    top: 300px;
    width: 5px;
    height: 125px;
    background: var(--brand-yellow);
  }
  .contact {
    position: absolute;
    left: 358px;
    top: 300px;
  }
  .contact-name {
    font-size: 19px;
    font-weight: 700;
    color: var(--brand-blue);
    margin-left: 26px;
    line-height: 1.2;
  }
  .contact-title {
    font-size: 16px;
    font-weight: 700;
    color: var(--brand-blue);
    margin-left: 30px;
    margin-top: 4px;
    line-height: 1.2;
  }
  .contact-list {
    list-style: none;
    margin-top: 10px;
  }
  .contact-list li {
    display: flex;
    align-items: center;
    gap: 9px;
    height: 27px;
    font-size: 14px;
    font-weight: 700;
    color: var(--text-yellow);
  }
  .contact-icon {
    width: 23px;
    height: 20px;
    flex: none;
  }
</style>
</head>
<body>
<main class="canvas">
  <section class="card card--front" aria-label="Card front">
    <div class="front-brand">
      <span class="brand-dot" aria-hidden="true"></span>
      <span class="brand-name">Query Lanterns</span>
    </div>
  </section>

  <section class="card card--back" aria-label="Card back">
    <div class="back-brand">
      <span class="brand-dot" aria-hidden="true"></span>
      <span class="brand-name">Query Lanterns</span>
    </div>
    <div class="divider" aria-hidden="true"></div>
    <div class="contact">
      <p class="contact-name">Liam Carver</p>
      <p class="contact-title">Internet Marketing Consultant</p>
      <ul class="contact-list">
        <li>
          <svg class="contact-icon" viewBox="0 0 24 20" aria-hidden="true">
            <g fill="none" stroke="var(--deep-blue)" stroke-width="1.8">
              <circle cx="12" cy="10" r="8.5"/>
              <ellipse cx="12" cy="10" rx="3.8" ry="8.5"/>
              <line x1="3.5" y1="10" x2="20.5" y2="10"/>
              <path d="M5 5.5h14M5 14.5h14"/>
            </g>
          </svg>
          www.querylanterns.com.au
        </li>
        <li>
          <svg class="contact-icon" viewBox="0 0 24 20" aria-hidden="true">
            <rect x="1.5" y="4" width="21" height="14" fill="var(--deep-blue)"/>
            <path d="M1.5 4 L12 12 L22.5 4" fill="none" stroke="#fff" stroke-width="1.6"/>
          </svg>
          liam@querylanterns.com.au
        </li>
        <li>
          <svg class="contact-icon" viewBox="0 0 24 20" aria-hidden="true">
            <path d="M2 7 Q12 0 22 7 L19 9.5 L16 7.5 L16 5.5 Q12 4 8 5.5 L8 7.5 L5 9.5 Z" fill="var(--deep-blue)"/>
            <rect x="6" y="10" width="12" height="8" rx="2" fill="var(--deep-blue)"/>
            <circle cx="12" cy="14" r="2" fill="#fff"/>
          </svg>
          1300 555 018
        </li>
      </ul>
    </div>
  </section>
</main>
</body>
</html>
```